Hacienda Monte Verda Business cards

We would like 3 individual business cards with the logo you designed:

1) Marta Pellingford - Phone: 206 555 0147
2) Theodore R Pellingford - Phone 206 555 0183
3) Dana Moreth - Phone 310-555-0162

Address for all three cards:
7218 142nd Ave NE
Carnation, WA 98014
HaciendaMonteVerda@brindlemail.com

```html
<!DOCTYPE html>
<html lang="en">
<head>
<meta charset="utf-8">
<title>Hacienda Monte Verda — Business Card</title>
<link href="https://fonts.googleapis.com/css2?family=Cinzel:wght@400;600&family=Open+Sans:wght@400&display=swap" rel="stylesheet">
<style>
  :root {
    --page-bg: #ebe9e7;
    --card-bg: #ffffff;
    --ink: #111111;
    --band: #0d0d0d;
    --band-text: #e6e6e6;
    --illustration: #2a2a2a;
  }
  * { margin: 0; padding: 0; box-sizing: border-box; }
  html, body {
    width: 1200px;
    height: 997px;
    overflow: hidden;
    background: var(--page-bg);
  }
  .canvas {
    position: relative;
    width: 1200px;
    height: 997px;
  }
  .business-card {
    position: absolute;
    left: 180px;
    top: 258px;
    width: 840px;
    height: 480px;
    background: var(--card-bg);
    box-shadow: 0 2px 10px rgba(0,0,0,0.08);
  }
  .brand-illustration {
    position: absolute;
    left: 300px;
    top: 56px;
    width: 280px;
    height: 104px;
    display: block;
  }
  .brand-name {
    position: absolute;
    left: 0;
    top: 182px;
    width: 100%;
    text-align: center;
    font-family: "Cinzel", serif;
    font-weight: 600;
    font-size: 38px;
    letter-spacing: 1px;
    color: var(--ink);
  }
  .name-band {
    position: absolute;
    left: 0;
    top: 262px;
    width: 100%;
    height: 58px;
    background: var(--band);
    display: flex;
    align-items: center;
    justify-content: center;
  }
  .holder-name {
    font-family: "Cinzel", serif;
    font-weight: 400;
    font-size: 22px;
    letter-spacing: 1.5px;
    color: var(--band-text);
  }
  .contact {
    position: absolute;
    left: 200px;
    top: 346px;
    font-family: "Open Sans", sans-serif;
    font-size: 21px;
    line-height: 32px;
    color: var(--ink);
  }
  .contact .phone { margin-right: 14px; }
</style>
</head>
<body>
<main class="canvas">
  <section class="business-card">
    <svg class="brand-illustration" viewBox="0 0 280 104" role="img" aria-label="Ranch illustration: oak tree beside a wooden fence with horses and birds in flight">
      <defs>
        <linearGradient id="illustrationTone" x1="0" y1="0" x2="1" y2="0">
          <stop offset="0" stop-color="#1e1e1e"/>
          <stop offset="1" stop-color="#5a5a5a"/>
        </linearGradient>
      </defs>
      <rect x="0" y="0" width="280" height="104" rx="6" fill="url(#illustrationTone)"/>
    </svg>

    <div class="brand-name">Hacienda Monte Verda</div>

    <div class="name-band">
      <span class="holder-name">Marta Pellingford</span>
    </div>

    <address class="contact">
      <div><span class="phone">P: 206 555 0147</span> HaciendaMonteVerda@brindlemail.com</div>
      <div>7218 142nd Ave NE Carnation, WA 98014</div>
    </address>
  </section>
</main>
</body>
</html>
```